Torvane Email Signature Banners – Fabrication Capability Series

www.Torvane.com.au is an Australian engineering and fabrication company specialising in fabrication and welding of :
steel piping spools,
skids and frames,
small volume process steel tanks
and general steel fabrication
We require four distinct banner designs for use in Microsoft Lintaro email signatures. Each banner will highlight a specific capability while maintaining a consistent brand identity.
Deliverables
Four banners total:
Piping Spools Fabrication – focus on precision welding and stainless steel pipework
Skid & Frames Fabrication – highlight skid systems and structural frames
Small Steel Tanks Fabrication – show fabricated tanks and workshop craftsmanship
General Fabrication Solutions – broad steel fabrication theme for company-wide use
Dimensions: 600–700 px wide × 100 px high
Format: PNG (preferred), small file size prefered
Resolution: 72 dpi
Background: non-transparent, industrial or workshop setting
Text examples:
1. Piping Spools Fabrication
Option A: “Expert Fabrication Solutions for Process Piping”
Option B: “Precision Welding for Complex Systems”
Option C: “Delivering Quality in Every Spool”
Option D: “Engineered for Flow, Built for Strength”
2. Skid & Frames Fabrication
Option A: “Custom Engineered Modular Systems”
Option B: “Built Strong. Designed Smart.”
Option C: “Reliable Frames for Industrial Performance”
Option D: “Modular Fabrication for Seamless Integration”
3. Small Steel Tanks Fabrication
Option A: “Precision Built for Your Needs”
Option B: “Compact Strength. Proven Durability.”
Option C: “Fabricated for Performance and Longevity”
Option D: “Small Tanks. Big Reliability.”
4. General Fabrication Solutions
Option A: “Quality Craftsmanship, Proven Results”
Option B: “Your Partner in Precision Fabrication”
Option C: “Engineering Excellence in Every Weld”
Option D: “Australian Fabrication. Global Standards.”
Style Direction
Clean, professional, and engineering‑focused
Use Torvane brand colours
Blend photo realism with vector clarity (no heavy gradients)
Include subtle industrial textures or workshop imagery
Typography: bold sans‑serif, legible at small scale
Usage Context
These banners will appear at the bottom of staff email signatures via Lintaro Email Signature Tool for Microsoft 365, so clarity and fast loading are essential. No Logo is required in the banners.
Reference
Existing Torvane signature is attached. Colour palette to match the signature style and logo.
Target Market(s)
Engineering and construction companies,
Industry/Entity Type
Engineering fabrication design
Look and feel

```html
<!DOCTYPE html>
<html lang="en">
<head>
<meta charset="utf-8">
<title>Torvane Email Signature Banners</title>
<link href="https://fonts.googleapis.com/css2?family=Poppins:wght@700&display=swap" rel="stylesheet">
<style>
  :root {
    --canvas-bg: #ffffff;
    --charcoal: #3b3b3c;
    --brand-blue: #29a3dd;
    --ink: #111111;
    --white: #ffffff;
    --steel-dark: #2c3740;
    --steel-mid: #6d7c88;
    --steel-light: #b9c4cc;
    --workshop-blue: #3d5f80;
    --furnace-orange: #c8743a;
  }
  * { box-sizing: border-box; margin: 0; padding: 0; }
  html, body { width: 1200px; height: 520px; overflow: hidden; background: var(--canvas-bg); }
  .canvas { position: relative; width: 1200px; height: 520px; }
  .banner {
    position: absolute; left: 57px; width: 1074px; height: 179px; overflow: hidden;
    font-family: "Poppins", sans-serif; font-weight: 700; text-transform: uppercase;
  }
  .banner--piping { top: 58px; background: var(--charcoal); }
  .banner--general { top: 278px; background: var(--brand-blue); }
  .banner__photo { position: absolute; top: 0; right: 0; bottom: 0; width: 470px; }
  .banner--piping .banner__photo {
    background: linear-gradient(90deg, var(--charcoal) 0%, rgba(59,59,60,0) 28%),
                linear-gradient(160deg, var(--steel-light) 0%, var(--steel-mid) 40%, var(--steel-dark) 100%);
  }
  .banner--general .banner__photo {
    background: linear-gradient(90deg, var(--brand-blue) 0%, rgba(41,163,221,0) 30%),
                linear-gradient(180deg, var(--furnace-orange) 0%, var(--workshop-blue) 35%, var(--steel-mid) 70%, var(--steel-dark) 100%);
  }
  .banner__text { position: absolute; left: 55px; top: 0; font-size: 37px; line-height: 1; letter-spacing: -0.2px; }
  .banner__line { position: absolute; left: 0; white-space: nowrap; }
  .banner__line--first { top: 42px; }
  .banner__line--second { top: 104px; }
  .banner--piping .banner__line--first { color: var(--brand-blue); }
  .banner--piping .banner__line--second { color: var(--white); }
  .banner--general .banner__line--first { color: var(--ink); }
  .banner--general .banner__line--second { color: var(--white); }
  .gap { display: inline-block; width: 82px; }
</style>
</head>
<body>
<main class="canvas">
  <section class="banner banner--piping">
    <div class="banner__photo" role="img" aria-label="Welder in protective gear fabricating large stainless steel process pipe in a workshop"></div>
    <div class="banner__text">
      <p class="banner__line banner__line--first">Expert Fabrication</p>
      <p class="banner__line banner__line--second">Solutions for Process Piping</p>
    </div>
  </section>
  <section class="banner banner--general">
    <div class="banner__photo" role="img" aria-label="Steel mill interior with rows of stacked steel pipes"></div>
    <div class="banner__text">
      <p class="banner__line banner__line--first">I<span class="gap"></span>General</p>
      <p class="banner__line banner__line--second">Fabrication Solutions</p>
    </div>
  </section>
</main>
</body>
</html>
```